Business card for a new cabinet shop company named Veloran Cabinets for high end cabinets

Design a business card, thinking dark rich green with colours to speak of high end luxury ie; cream, gold, black possibly

Mitchell Tarrowby
Director Craftsman
Email: info@veloranjoinery-example.com.au
Instagram : @veloran.cabinets

```html
<!DOCTYPE html>
<html lang="en">
<head>
<meta charset="utf-8">
<title>Veloran Cabinets – Business Card</title>
<link rel="stylesheet" href="https://fonts.googleapis.com/css2?family=Montserrat:wght@400;500;700&display=swap">
<style>
  :root {
    --backdrop: #161616;
    --card-green: #1f3d3b;
    --gold: #c9a965;
    --cream: #ffffff;
  }
  * { margin: 0; padding: 0; box-sizing: border-box; }
  html, body {
    width: 1200px;
    height: 1059px;
    overflow: hidden;
    background: var(--backdrop);
    font-family: "Montserrat", sans-serif;
  }
  .canvas {
    position: relative;
    width: 1200px;
    height: 1059px;
  }
  .card {
    position: absolute;
    background: var(--card-green);
    border-radius: 28px;
    box-shadow: 0 10px 28px rgba(0,0,0,0.55);
    overflow: hidden;
  }
  .card--front { left: 258px; top: 99px; width: 688px; height: 392px; }
  .card--back  { left: 258px; top: 553px; width: 693px; height: 395px; }

  .wordmark {
    color: var(--gold);
    font-weight: 500;
    line-height: 1;
  }
  .wordmark__main { display: block; font-size: 72px; letter-spacing: 0.5px; }
  .wordmark__sub {
    display: block;
    font-size: 30px;
    letter-spacing: 16px;
    text-transform: uppercase;
    margin-top: 14px;
  }

  .card--front .wordmark {
    position: absolute;
    left: 52px;
    top: 40px;
  }

  .contact-block {
    position: absolute;
    left: 40px;
    top: 214px;
  }
  .person-name {
    color: var(--gold);
    font-weight: 700;
    font-size: 26px;
    letter-spacing: 0.2px;
  }
  .person-role {
    color: var(--cream);
    font-size: 18px;
    font-weight: 400;
    margin-top: 7px;
  }
  .contact-list { list-style: none; margin-top: 16px; }
  .contact-item {
    display: flex;
    align-items: center;
    gap: 10px;
    color: var(--cream);
    font-size: 18.5px;
    font-weight: 400;
    height: 36px;
  }
  .contact-icon { width: 20px; height: 20px; flex: none; }

  .card--back .wordmark {
    position: absolute;
    left: 0;
    right: 0;
    top: 50%;
    transform: translateY(-50%);
    text-align: center;
  }
  .card--back .wordmark__main { font-size: 80px; }
  .card--back .wordmark__sub { font-size: 32px; letter-spacing: 18px; margin-right: -18px; }
</style>
</head>
<body>
<main class="canvas">
  <section class="card card--front" aria-label="Business card front">
    <h1 class="wordmark">
      <span class="wordmark__main">Veloran</span>
      <span class="wordmark__sub">Cabinets</span>
    </h1>
    <div class="contact-block">
      <p class="person-name">Mitchell Tarrowby</p>
      <p class="person-role">Director Craftsman</p>
      <ul class="contact-list">
        <li class="contact-item">
          <svg class="contact-icon" viewBox="0 0 20 20" aria-hidden="true">
            <rect x="1" y="4" width="18" height="12" fill="var(--gold)"/>
            <path d="M1 4 L10 11 L19 4" fill="none" stroke="var(--card-green)" stroke-width="1.6"/>
          </svg>
          <span>info@veloranjoinery-example.com.au</span>
        </li>
        <li class="contact-item">
          <svg class="contact-icon" viewBox="0 0 20 20" aria-hidden="true">
            <circle cx="10" cy="10" r="8" fill="none" stroke="var(--gold)" stroke-width="2"/>
          </svg>
          <span>@veloran.cabinets</span>
        </li>
      </ul>
    </div>
  </section>

  <section class="card card--back" aria-label="Business card back">
    <h2 class="wordmark">
      <span class="wordmark__main">Veloran</span>
      <span class="wordmark__sub">Cabinets</span>
    </h2>
  </section>
</main>
</body>
</html>
```